Marcus Delbridge Finance

Need a personal website advertising Equipment Finance,Business Finance,Commercial Finance, Construction Finance, Bridging Finance. Similar websites are www.corvalend.com.au / www.tarmivest.com.au / www.qbr7.com.au /wwwhalvecredit.com.au

Target Market(s)

Business People

Industry/Entity Type

Business

Number of Pages Required

3 page

Font styles to use
Serif
Sans Serif

Requirements
Must have
• All i want is a simple corporate looking website advertising Equipment Finance, Commercial Finance, Construction Finance, Business Finance, Bridging Finance,

```html
<!DOCTYPE html>
<html lang="en">
<head>
<meta charset="utf-8">
<title>Marcus Delbridge Finance</title>
<link rel="stylesheet" href="https://fonts.googleapis.com/css2?family=Cinzel:wght@400;700&family=Open+Sans:wght@300;400;600;700&display=swap">
<style>
:root{
  --blue:#0a7ad1;
  --blue-text:#0b6fc0;
  --ink:#1c1c1c;
  --body:#333;
  --light:#f7f7f7;
  --band:#ebebeb;
  --footer:#1d1f22;
  --label:rgba(40,40,40,.82);
  --white:#fff;
}
*{margin:0;padding:0;box-sizing:border-box}
html,body{width:1006px;height:1200px;overflow:hidden}
body{position:relative;background:var(--light);font-family:"Open Sans",Arial,sans-serif;color:var(--body)}
.abs{position:absolute}
.serif{font-family:"Cinzel",Georgia,serif}

.site-header{left:0;top:0;width:1006px;height:85px;background:var(--white)}
.brand{left:33px;top:22px;display:flex;align-items:center;gap:12px}
.brand-mark{width:30px;height:30px;background:var(--ink)}
.brand-name{font-family:"Cinzel",Georgia,serif;font-size:21px;line-height:26px;color:var(--ink);letter-spacing:.5px}
.call{right:33px;top:26px;display:flex;align-items:center;gap:8px}
.call-lines{line-height:1}
.call-label{font-family:"Cinzel",Georgia,serif;font-size:12px;color:var(--blue-text)}
.call-number{font-size:19px;color:var(--ink);margin-top:3px}

.main-nav{left:0;top:85px;width:1006px;height:45px;background:var(--blue);display:flex;align-items:center;justify-content:space-between;padding:0 33px 0 33px}
.main-nav a{color:var(--white);text-decoration:none;font-size:16px;font-weight:300;text-transform:uppercase;height:45px;line-height:45px;padding:0 14px}
.main-nav a.active{background:#111}

.tile{overflow:hidden;border-right:1px solid #bbb}
.tile-art{position:absolute;inset:0}
.tile-label{position:absolute;left:0;right:0;bottom:0;background:var(--label);color:var(--white);font-weight:700;font-size:17px;text-align:center}
.tile-label.tall{height:41px;line-height:41px}
.tile-label.short{height:33px;line-height:33px;font-size:16px}

.about{left:0;top:502px;width:1006px;height:266px;text-align:center}
.about h1{font-family:"Cinzel",Georgia,serif;font-weight:400;font-size:27px;margin-top:32px;color:var(--ink);letter-spacing:.5px}
.about h1 span{color:var(--blue-text)}
.about p{font-size:12.3px;line-height:20.5px;color:var(--body);width:930px;margin:24px auto 0}
.btn{display:inline-block;margin-top:32px;background:#e2e2e2;border-radius:3px;padding:0 13px;height:36px;line-height:36px;font-size:12.5px;color:var(--ink)}

.customers{left:0;top:768px;width:1006px;height:106px;background:var(--band)}
.customers-title{left:15px;top:34px;font-family:"Cinzel",Georgia,serif;font-size:19px;line-height:22px;color:var(--ink);text-align:right;width:116px}
.partner{top:32px;width:127px;height:60px;background:var(--white);border:1px solid #d4d4d4;display:flex;align-items:center;justify-content:center;font-weight:700;font-size:14px;color:#444}

.site-footer{left:0;top:874px;width:1006px;height:281px;background:linear-gradient(180deg,#2a2c30,#151618)}
.footer-col h3{font-family:"Cinzel",Georgia,serif;font-weight:400;font-size:18px;color:var(--white);padding-bottom:10px;border-bottom:1px solid #555;position:relative}
.footer-col h3::after{content:"";position:absolute;left:0;bottom:-1px;width:22px;height:1px;background:var(--blue)}
.quick-links{list-style:none;margin-top:12px}
.quick-links li{font-size:11.5px;color:#ddd;height:28px;line-height:28px}
.quick-links li::before{content:"›";color:#aaa;margin-right:7px}
.quick-links li.active{color:#3d9be6}
.contact-row{display:flex;gap:9px;color:#ddd;font-size:11.5px;line-height:15px}
.contact-row strong{color:var(--white);font-weight:600}
.map{left:539px;top:965px;width:219px;height:148px;border:3px solid var(--white);background:linear-gradient(135deg,#e9ecef 0%,#dfe6dd 55%,#cfe3b8 100%)}
.footer-brand{left:800px;top:1052px;width:180px;text-align:center;font-family:"Cinzel",Georgia,serif;font-size:22px;line-height:28px;color:var(--white)}

.bottom-bar{left:0;top:1155px;width:1006px;height:45px;background:var(--blue);color:var(--white);font-size:12px;line-height:45px;padding-left:70px}
.bottom-bar strong{font-weight:600}
.social{right:40px;top:1161px;display:flex;gap:5px}
.social span{width:32px;height:32px;border-radius:50%;border:2px solid var(--white);display:block}
</style>
</head>
<body>

<header class="site-header abs">
  <div class="brand abs">
    <span class="brand-mark"></span>
    <div class="brand-name">Marcus Delbridge<br>Finance</div>
  </div>
  <div class="call abs">
    <svg width="38" height="38" viewBox="0 0 38 38" aria-hidden="true">
      <circle cx="19" cy="19" r="17" fill="none" stroke="#0b6fc0" stroke-width="2.5"/>
      <path d="M13 11c2-1 3 0 4 3s-1 3-1 4 3 5 4 5 2-2 3-1 3 2 3 3-2 3-4 3c-5 0-11-8-11-12 0-2 1-4 2-5z" fill="#0b6fc0"/>
    </svg>
    <div class="call-lines">
      <div class="call-label">Call Us Today</div>
      <div class="call-number">123-555-0148</div>
    </div>
  </div>
</header>

<nav class="main-nav abs">
  <a class="active">Home</a><a>About Us</a><a>Our Services</a><a>Resources</a><a>Latest News</a><a>Contact Us</a>
</nav>

<section class="services">
  <div class="tile abs" style="left:0;top:130px;width:235px;height:372px">
    <div class="tile-art" role="img" aria-label="Yellow wheel loader on a white background" style="background:linear-gradient(160deg,#f2f2f2 0%,#e4d9a8 45%,#c9a52a 70%,#e9e9e9 100%)"></div>
    <div class="tile-label tall">Equipment Finance</div>
  </div>
  <div class="tile abs" style="left:235px;top:130px;width:268px;height:186px">
    <div class="tile-art" role="img" aria-label="Business people talking in a bright office" style="background:linear-gradient(160deg,#dfe7ec 0%,#aab6bf 50%,#4f5a63 100%)"></div>
    <div class="tile-label short">Business Finance</div>
  </div>
  <div class="tile abs" style="left:503px;top:130px;width:268px;height:186px">
    <div class="tile-art" role="img" aria-label="Handshake in front of office towers" style="background:linear-gradient(170deg,#1d2d55 0%,#4b6a9c 50%,#a7b9cf 100%)"></div>
    <div class="tile-label short">Commercial Finance</div>
  </div>
  <div class="tile abs" style="left:235px;top:316px;width:536px;height:186px">
    <div class="tile-art" role="img" aria-label="Construction worker holding a yellow hard hat and plans at a building site" style="background:linear-gradient(90deg,#8e949a 0%,#b5b0a2 45%,#d2b23a 70%,#5d7594 100%)"></div>
    <div class="tile-label tall">Construction Finance</div>
  </div>
  <div class="tile abs" style="left:771px;top:130px;width:235px;height:372px;border-right:0">
    <div class="tile-art" role="img" aria-label="Figure placing a blue puzzle piece into a white puzzle wall" style="background:radial-gradient(circle at 55% 55%,#2f6fd0 0%,#8fa9d6 18%,#e2e2e2 45%,#f4f4f4 100%)"></div>
    <div class="tile-label tall">Bridging Finance</div>
  </div>
</section>

<section class="about abs">
  <h1>About Marcus Delbridge <span>Finance</span></h1>
  <p>Lorem ipsum dolor sit amet, consectetuer adipiscing elit, sed diam nonummy nibh euismod tincidunt ut laoreet dolore magna aliquam erat volutpat. Ut wisi enim ad minim veniam, quis nostrud exerci tation ullamcorper suscipit lobortis nisl ut aliquip ex ea commodo consequat. Duis autem vel eum iriure dolor in hendrerit in vulputate velit esse molestie consequat, vel illum dolore eu feugiat nulla facilisis at vero eros et accumsan et iusto odio dignissim qui blandit praesent luptatum zzril delenit augue duis dolore te feugait nulla facilisi.</p>
  <span class="btn">Read More</span>
</section>

<section class="customers abs">
  <div class="customers-title abs">Our<br>Customers</div>
  <svg class="abs" style="left:138px;top:20px" width="28" height="68" viewBox="0 0 28 68" aria-hidden="true">
    <path d="M2 2 L26 34 L2 66 L12 34 Z" fill="#b5b5b5"/>
  </svg>
  <div class="partner abs" style="left:185px">Voltaris</div>
  <div class="partner abs" style="left:333px">Kestrel</div>
  <div class="partner abs" style="left:482px">Brandt</div>
  <div class="partner abs" style="left:631px">Ovenor</div>
  <div class="partner abs" style="left:780px">Lindqvist Power</div>
  <svg class="abs" style="left:923px;top:38px" width="52" height="46" viewBox="0 0 52 46" aria-hidden="true">
    <path d="M20 4 L4 23 L20 42 M32 4 L48 23 L32 42" fill="none" stroke="#cfcfcf" stroke-width="2"/>
  </svg>
</section>

<footer class="site-footer abs">
  <div class="footer-col abs" style="left:70px;top:46px;width:156px">
    <h3>Quick Links</h3>
    <ul class="quick-links">
      <li class="active">Home</li><li>About Us</li><li>Our Services</li><li>Resources</li><li>Latest News</li><li>Contact Us</li>
    </ul>
  </div>
  <div class="footer-col abs" style="left:275px;top:46px;width:210px">
    <h3>Contact Detail</h3>
    <div class="contact-row" style="margin-top:14px">
      <svg width="12" height="16" viewBox="0 0 12 16" aria-hidden="true"><path d="M6 0a6 6 0 0 1 6 6c0 4-6 10-6 10S0 10 0 6a6 6 0 0 1 6-6z" fill="#2f8fe0"/><circle cx="6" cy="6" r="2.2" fill="#1d1f22"/></svg>
      <div><strong>Marcus Delbridge Finance</strong><br>418 Harlow Street, Suite 210<br>Brookvale, NT 0812</div>
    </div>
    <div class="contact-row" style="margin-top:30px;font-size:13.5px">
      <svg width="12" height="14" viewBox="0 0 12 14" aria-hidden="true"><path d="M2 1c1-1 2 0 3 2s-1 2 0 4 2 3 3 3 1-1 2 0 2 1 2 2-1 2-3 2C5 14 0 7 0 4c0-1 1-2 2-3z" fill="#2f8fe0"/></svg>
      <span>123-555-0148</span>
    </div>
    <div class="contact-row" style="margin-top:38px;font-size:12px">
      <svg width="14" height="11" viewBox="0 0 14 11" aria-hidden="true"><rect width="14" height="11" rx="1" fill="#2f8fe0"/><path d="M0 1 L7 6 L14 1" fill="none" stroke="#1d1f22" stroke-width="1.3"/></svg>
      <span>info@delbridgefinance.com</span>
    </div>
  </div>
  <div class="footer-col abs" style="left:537px;top:46px;width:223px">
    <h3>Location Map</h3>
  </div>
  <div class="footer-brand abs">Marcus Delbridge<br>Finance</div>
</footer>
<div class="map abs" role="img" aria-label="Street map showing the office location"></div>

<div class="bottom-bar abs">Copyright © 2016 <strong>Marcus Delbridge Finance</strong> . All Rights Reserved.</div>
<div class="social abs" role="img" aria-label="Social media links">
  <span style="background:#3b5998"></span><span style="background:#1da1f2"></span><span style="background:#0e76a8"></span><span style="background:#dd3b2b"></span>
</div>

</body>
</html>
```